Poster for Office

Looking for an edgy, beautiful poster to hang up in my office that uses the quotes located below and potentially the image attached.
Content for poster

Title: Prewitt's Maxims

Must have the following quotes included (punctuation and capitalization are flexible, do what you think looks the best they also don't need the quotation symbols):

"Don't order fish at a steakhouse"
"Be bold. The more you tell, the more you sell"
"admit nothing, deny everything, launch counterattack."
"avoid obviousness"
"never do anything until you're ready to do it"
"look good=feel good"
"always keep the advantage"
"never complain, never explain"
"Lay low, play dumb, keep moving"

Quotes

• Title: Prewitt's Maxims

"avoid obviousness"
"look good=feel good"

```html
<!DOCTYPE html>
<html lang="en">
<head>
<meta charset="utf-8">
<title>Prewitt's Maxims</title>
<link rel="stylesheet" href="https://fonts.googleapis.com/css2?family=Anton&display=swap">
<style>
  :root {
    --paper: #ffffff;
    --photo-light: #f4f4f4;
    --photo-mid: #d6d6d6;
    --photo-dark: #a9a9a9;
    --blue-title: #2b5cf0;
    --blue-strong: #2c52e4;
    --blue-soft: #5b8de8;
    --blue-deep: #1a2fd2;
    --blue-sky: #6ea6f6;
    --blue-royal: #2443d8;
    --blue-lilac: #6a82e8;
    --blue-cyan: #4fb2ee;
    --blue-ink: #1522d6;
  }
  html, body {
    margin: 0;
    padding: 0;
    overflow: hidden;
    background: var(--paper);
  }
  .poster {
    position: relative;
    width: 854px;
    height: 1200px;
    overflow: hidden;
    background: var(--paper);
  }
  .photo-backdrop {
    position: absolute;
    inset: 0;
    background:
      radial-gradient(ellipse 34% 40% at 50% 22%, var(--paper) 0%, rgba(255,255,255,0) 100%),
      linear-gradient(90deg, var(--photo-dark) 0%, var(--photo-mid) 22%, var(--photo-light) 50%, var(--photo-mid) 78%, var(--photo-dark) 100%);
  }
  .maxims {
    position: absolute;
    inset: 0;
    font-family: "Anton", "Impact", sans-serif;
  }
  .maxims text { font-family: "Anton", "Impact", sans-serif; }
  .title { fill: var(--blue-title); font-size: 100px; }
  .m-fish { fill: var(--blue-strong); font-size: 52px; }
  .m-bold { fill: var(--blue-soft); font-size: 38px; }
  .m-admit { fill: var(--blue-deep); font-size: 34px; }
  .m-obvious { fill: var(--blue-sky); font-size: 90px; }
  .m-ready { fill: var(--blue-royal); font-size: 44px; }
  .m-look { fill: var(--blue-lilac); font-size: 80px; }
  .m-advantage { fill: var(--blue-cyan); font-size: 46px; }
  .m-complain { fill: var(--blue-strong); font-size: 58px; }
  .m-lay { fill: var(--blue-ink); font-size: 44px; }
</style>
</head>
<body>
<main class="poster">
  <div class="photo-backdrop" role="img" aria-label="Black-and-white photograph of two shirtless men standing back to back"></div>
  <svg class="maxims" width="854" height="1200" viewBox="0 0 854 1200" xmlns="http://www.w3.org/2000/svg">
    <text class="title" x="60" y="235" textLength="728" lengthAdjust="spacingAndGlyphs">Prewitt's Maxims</text>
    <text class="m-fish" x="65" y="494" textLength="720" lengthAdjust="spacingAndGlyphs">Don't order fish at a steakhouse</text>
    <text class="m-bold" x="62" y="550" textLength="718" lengthAdjust="spacingAndGlyphs">Be bold. The more you tell, the more you sell</text>
    <text class="m-admit" x="60" y="603" textLength="712" lengthAdjust="spacingAndGlyphs">admit nothing, deny everything, launch counterattack</text>
    <text class="m-obvious" x="58" y="688" textLength="728" lengthAdjust="spacingAndGlyphs">avoid obviousness</text>
    <text class="m-ready" x="55" y="738" textLength="735" lengthAdjust="spacingAndGlyphs">never do anything until you're ready to do it</text>
    <text class="m-look" x="60" y="818" textLength="722" lengthAdjust="spacing">look good=feel good</text>
    <text class="m-advantage" x="55" y="866" textLength="725" lengthAdjust="spacing">always keep the advantage</text>
    <text class="m-complain" x="58" y="923" textLength="726" lengthAdjust="spacingAndGlyphs">never complain, never explain</text>
    <text class="m-lay" x="58" y="983" textLength="730" lengthAdjust="spacing">lay low, play dumb, keep moving</text>
  </svg>
</main>
</body>
</html>
```